DL SIZED ONE SIDED BROCHURE FOR CLEANING AND GARDENING SERVICE

business name: K&T property services
services provided: Strata cleaning,lawn mowing,hedge trimming,garden maintainance,lawn repair,weed spraying/removal, rubbish removal.
10 years experience and fully insured.
obligation free quotes.
phone number:contact dennis 0427903516
email: ktpropertyservices@mailvexo.com
slogan: when quality matters ring K&T
K&T logo would be nice but not essential
DL size in inches: 3.9in × 8.2in
DL size in millimetres: 100mm × 210mm
DL size in centimetres: 10cm x 21cm
Updates
doing good guys no suggestions except being original
Target Market(s)
real estate agents, private home owners, contractors.
Industry/Entity Type
Business
Look and feel
Each slider illustrates characteristics of the customer's brand and the style your logo design should communicate.

```html
<!DOCTYPE html>
<html lang="en">
<head>
<meta charset="utf-8">
<title>K&amp;T Property Services – DL Brochure</title>
<link rel="stylesheet" href="https://fonts.googleapis.com/css2?family=Mulish:wght@400;600;700;800&family=Kristi&display=swap">
<style>
  :root {
    --ink: #231f20;
    --panel: #2a2627;
    --white: #ffffff;
    --blue: #00aeef;
    --band-text: #1d1a1b;
    --photo-light: #d6d6d6;
    --photo-mid: #9a9a9a;
    --photo-dark: #5a5a5a;
  }
  * { box-sizing: border-box; margin: 0; padding: 0; }
  html, body { width: 1200px; height: 571px; overflow: hidden; background: var(--white); }
  .brochure {
    position: relative;
    width: 1200px;
    height: 571px;
    font-family: "Mulish", "Helvetica Neue", Arial, sans-serif;
    color: var(--white);
  }

  /* Photo collage */
  .collage { position: absolute; left: 0; top: 0; width: 678px; height: 503px; }
  .photo { position: absolute; }
  .photo--hedge-worker { left: 0; top: 0; width: 340px; height: 250px;
    background: linear-gradient(135deg, var(--photo-light), var(--photo-mid) 60%, var(--photo-dark)); }
  .photo--mower { left: 340px; top: 0; width: 338px; height: 250px;
    background: linear-gradient(200deg, var(--photo-light), var(--photo-mid) 55%, var(--photo-dark)); }
  .photo--trimmer { left: 0; top: 250px; width: 340px; height: 253px;
    background: linear-gradient(160deg, var(--photo-mid), var(--photo-light) 50%, var(--photo-mid)); }
  .photo--cleaning { left: 340px; top: 250px; width: 338px; height: 253px;
    background: linear-gradient(120deg, var(--photo-light), #bdbdbd 50%, var(--photo-mid)); }

  /* Name block */
  .name-block {
    position: absolute; left: 197px; top: 103px; width: 293px; height: 294px;
    background: var(--ink);
    display: flex; flex-direction: column; align-items: center; justify-content: center;
    font-weight: 600; color: var(--white); text-align: center;
  }
  .name-block__name { font-size: 118px; line-height: 1; letter-spacing: -4px; font-weight: 800; }
  .name-block__sub { margin-top: 14px; font-size: 31px; line-height: 1.18; font-weight: 800; }

  .slogan {
    position: absolute; left: 155px; top: 408px;
    font-family: "Kristi", cursive; font-size: 50px; color: var(--ink);
  }

  /* Services panel */
  .services { position: absolute; left: 678px; top: 0; width: 522px; height: 503px; background: var(--panel); }
  .services__title { position: absolute; left: 55px; top: 62px; font-size: 34px; font-weight: 400; }
  .services__list { position: absolute; left: 55px; top: 117px; list-style: none; }
  .services__item { position: relative; padding-left: 37px; font-size: 22px; line-height: 34.2px; font-weight: 400; }
  .services__item::before {
    content: ""; position: absolute; left: 4px; top: 13px; width: 8px; height: 8px; background: var(--white);
  }
  .contact { position: absolute; left: 55px; top: 374px; }
  .contact__lead { font-size: 21px; font-weight: 400; }
  .contact__phone { margin-top: 9px; font-size: 26px; font-weight: 800; color: var(--blue); }
  .contact__email { margin-top: 9px; font-size: 17px; font-weight: 400; }

  /* Footer band */
  .band {
    position: absolute; left: 0; top: 503px; width: 1200px; height: 68px;
    background: var(--blue); color: var(--band-text);
    display: flex; align-items: center; justify-content: center;
    font-size: 21px; font-weight: 800; letter-spacing: 4.3px;
  }
</style>
</head>
<body>
<main class="brochure">
  <section class="collage">
    <div class="photo photo--hedge-worker" role="img" aria-label="Black and white photo of a gardener trimming a tall hedge"></div>
    <div class="photo photo--mower" role="img" aria-label="Black and white photo of a man pushing a lawn mower across grass"></div>
    <div class="photo photo--trimmer" role="img" aria-label="Black and white photo of a hedge trimmer cutting a low hedge"></div>
    <div class="photo photo--cleaning" role="img" aria-label="Black and white photo of a bucket, mop, broom and cleaning supplies on a floor"></div>
    <div class="name-block">
      <div class="name-block__name">K&amp;T</div>
      <div class="name-block__sub">PROPERTY<br>SERVICES</div>
    </div>
    <p class="slogan">When quality matters</p>
  </section>

  <section class="services">
    <h2 class="services__title">Our services include...</h2>
    <ul class="services__list">
      <li class="services__item">Strata cleaning</li>
      <li class="services__item">Lawn mowing</li>
      <li class="services__item">Hedge trimming</li>
      <li class="services__item">Garden maintainance</li>
      <li class="services__item">Lawn repair</li>
      <li class="services__item">Weed spraying/removal</li>
      <li class="services__item">Rubbish removal</li>
    </ul>
    <div class="contact">
      <p class="contact__lead">For obligation free quote contact:</p>
      <p class="contact__phone">Dennis 0427 903 516</p>
      <p class="contact__email">ktpropertyservices@mailvexo.com</p>
    </div>
  </section>

  <footer class="band">10 YEARS EXPERIENCE &amp; FULLY INSURED</footer>
</main>
</body>
</html>
```